Local Roofing/Construction company business needs new biz card design

We need a new business card design, current cards are from the start of this operation and generic at best. We are a local Construction Company (General Contractor) with a majority of our work originating from insurance claims-exterior finish work is the main focus (Roofs-Siding-Gutters etc). Heavily involved with homeowners and the low ball offers they receive from insurance company's after a insurable event takes place. I have attached some of our original logo file(s) below.

```html
<!DOCTYPE html>
<html lang="en">
<head>
<meta charset="utf-8">
<title>Northgate Construction – Business Card</title>
<link href="https://fonts.googleapis.com/css2?family=Exo+2:wght@400;500;700&display=swap" rel="stylesheet">
<style>
  :root {
    --bg: #cfcfcf;
    --card: #0e1c21;
    --card-deep: #0c1a1e;
    --green: #2fd97a;
    --pattern: #11332a;
    --ink: #f2f4f3;
  }
  * { box-sizing: border-box; margin: 0; padding: 0; }
  html, body { width: 1200px; height: 800px; overflow: hidden; }
  body {
    background: var(--bg);
    font-family: "Exo 2", sans-serif;
    position: relative;
  }
  .card {
    position: absolute;
    left: 338px;
    width: 525px;
    height: 300px;
    background: var(--card);
    border: 2px solid var(--green);
    overflow: hidden;
  }
  .card--front { top: 70px; }
  .card--back { top: 430px; background: var(--card-deep); }

  .brand-badge {
    position: absolute;
    background: var(--green);
    border-radius: 18px;
    display: flex;
    align-items: center;
    justify-content: center;
    text-align: center;
    color: var(--ink);
    font-weight: 700;
    text-transform: uppercase;
    line-height: 1.1;
  }
  .card--front .brand-badge {
    left: 42px; top: 72px;
    width: 176px; height: 156px;
    font-size: 22px;
    letter-spacing: 1px;
  }
  .divider {
    position: absolute;
    left: 250px; top: 40px;
    width: 2px; height: 220px;
    background: var(--green);
  }
  .details {
    position: absolute;
    left: 276px; top: 56px;
    color: var(--ink);
    text-transform: uppercase;
  }
  .details__name {
    color: var(--green);
    font-weight: 700;
    font-size: 21px;
    letter-spacing: 0.5px;
  }
  .details__role {
    font-size: 14px;
    letter-spacing: 0.5px;
    margin-bottom: 18px;
  }
  .contact-list { list-style: none; font-size: 13px; line-height: 1.55; }
  .contact-list li { display: flex; align-items: center; gap: 7px; }
  .contact-list svg { width: 12px; height: 12px; flex: none; }
  .accent { color: var(--green); }
  .address { margin-top: 18px; font-size: 13px; line-height: 1.55; }

  .pattern-field {
    position: absolute; inset: 0;
    background: var(--pattern);
  }
  .card--back .brand-badge {
    right: 78px; top: 98px;
    width: 120px; height: 104px;
    font-size: 15px;
    border-radius: 14px;
  }
</style>
</head>
<body>

<section class="card card--front">
  <div class="brand-badge">Northgate<br>Construction</div>
  <div class="divider"></div>
  <div class="details">
    <p class="details__name">Daniel Hartley</p>
    <p class="details__role">Managing Director</p>
    <ul class="contact-list">
      <li>
        <svg viewBox="0 0 12 12"><path d="M2.5 1 4.5 1 5.3 3.5 4 4.4C4.6 5.8 6.2 7.4 7.6 8L8.5 6.7 11 7.5V9.5C11 10.3 10.3 11 9.5 11 5 11 1 7 1 2.5 1 1.7 1.7 1 2.5 1Z" fill="var(--green)"/></svg>
        044-987 650 321
      </li>
      <li>
        <svg viewBox="0 0 12 12"><rect x="0.5" y="2" width="11" height="8" fill="var(--green)"/><path d="M0.5 2 6 6.5 11.5 2" fill="none" stroke="var(--card)" stroke-width="1.2"/></svg>
        info@northgatebuild.com
      </li>
      <li>
        <svg viewBox="0 0 12 12"><circle cx="6" cy="6" r="5.2" fill="var(--green)"/><path d="M1 6H11M6 1V11M3 2.5C4.5 4.5 4.5 7.5 3 9.5M9 2.5C7.5 4.5 7.5 7.5 9 9.5" fill="none" stroke="var(--card)" stroke-width="0.8"/></svg>
        www.<span class="accent">northgatebuild</span>.com
      </li>
    </ul>
    <p class="address">421, Address Line Here<br>45452, Country Name</p>
  </div>
</section>

<section class="card card--back">
  <div class="pattern-field" role="img" aria-label="Faint repeating pattern of the company badge across the card back"></div>
  <div class="brand-badge">Northgate<br>Construction</div>
</section>

</body>
</html>
```